Computer Training in the Education sector - Letterhead

We need a new letter head to be designed for the company. We provide computer training fro the Education Sector, both primary and private tertiary providers. The colours will need to tie in with the website www.crossingthestream.co.nz.
The company name is Crossing the Stream with the tag line of Computer Training for Educators.
The footer will need to have the following detail...
0508 PCS MENTOR
021 839 415
www.crossingthestream.co.nz / training@crossingthestream.co.nz
Updates

Thanks for the designs so far.

Some have watermarks in the background. Please don't worry about using watermarks as I will not be using a watermark in in a final design.
Regards,
Roger

Thank you for all the designs and the effort. There was some great concepts that came through.

Cheers
Roger

Industry/Entity Type

Computer

```html
<!DOCTYPE html>
<html lang="en">
<head>
<meta charset="utf-8">
<title>Crossing the Stream – Letterhead and Business Card</title>
<link rel="stylesheet" href="https://fonts.googleapis.com/css2?family=Nunito:wght@700;800&family=Questrial&display=swap">
<style>
  :root {
    --bg-light: #fffbe6;
    --bg-warm: #fbe9a8;
    --band-gold: #f8d772;
    --band-pale: #fff7d6;
    --brand-blue: #5b8fe8;
    --brand-orange: #f39321;
    --rule-green: #11c41a;
    --ink: #111111;
    --paper: #ffffff;
    --edge: #c9c2a8;
  }
  * { box-sizing: border-box; margin: 0; padding: 0; }
  html, body { width: 1200px; height: 1000px; overflow: hidden; }
  body {
    background: radial-gradient(ellipse at 62% 48%, var(--bg-light) 0%, var(--bg-warm) 100%);
    font-family: "Questrial", "Century Gothic", sans-serif;
    color: var(--ink);
    position: relative;
  }

  /* ---------- shared ---------- */
  .wordmark {
    font-family: "Nunito", sans-serif;
    font-weight: 800;
    color: var(--brand-blue);
    display: flex;
    align-items: center;
    gap: 8px;
    line-height: 1.05;
  }
  .wordmark-dot {
    flex: none;
    border-radius: 50%;
    background: var(--brand-blue);
  }
  .contact-list { list-style: none; }
  .contact-list li {
    display: flex;
    align-items: center;
    gap: 12px;
    font-weight: 700;
    font-size: 11px;
    line-height: 1;
    -webkit-text-stroke: 0.3px var(--ink);
  }
  .contact-list svg { width: 14px; height: 14px; flex: none; }

  /* ---------- letterhead ---------- */
  .letterhead {
    position: absolute;
    left: 70px; top: 90px;
    width: 560px; height: 800px;
    background: var(--paper);
    border: 1px solid var(--edge);
    display: flex;
    flex-direction: column;
  }
  .letterhead-header {
    position: relative;
    height: 170px;
    background: linear-gradient(90deg, var(--band-gold) 0%, var(--band-pale) 30%, var(--band-pale) 55%, var(--band-gold) 100%);
    border-bottom: 9px solid var(--rule-green);
  }
  .letterhead-header .wordmark {
    position: absolute;
    left: 24px; top: 38px;
    width: 110px;
    font-size: 20px;
    flex-direction: column;
    align-items: flex-start;
  }
  .letterhead-header .wordmark-dot { width: 22px; height: 22px; }
  .letterhead-title {
    position: absolute;
    left: 160px; top: 28px;
    font-family: "Nunito", sans-serif;
    font-weight: 800;
    font-size: 38px;
    color: var(--brand-blue);
    white-space: nowrap;
  }
  .letterhead-tagline {
    position: absolute;
    right: 36px; top: 84px;
    font-size: 12px;
  }
  .date-line {
    position: absolute;
    right: 36px; top: 124px;
    display: flex;
    align-items: flex-end;
    gap: 8px;
    font-weight: 700;
    font-size: 13px;
  }
  .date-line span.rule {
    display: block;
    width: 150px;
    border-bottom: 1.5px solid var(--ink);
  }
  .letterhead-body { flex: 1; }
  .letterhead-footer {
    height: 92px;
    background: linear-gradient(90deg, var(--band-gold) 0%, var(--band-pale) 40%, var(--band-pale) 60%, var(--band-gold) 100%);
    display: flex;
    justify-content: space-between;
    align-items: center;
    padding: 0 30px;
  }
  .letterhead-footer .contact-list li + li { margin-top: 9px; }

  /* ---------- business card ---------- */
  .business-card {
    position: absolute;
    left: 680px; top: 420px;
    width: 460px; height: 262px;
    background: var(--paper);
    border: 1px solid var(--edge);
    display: flex;
    flex-direction: column;
  }
  .card-main { flex: 1; position: relative; }
  .card-main .wordmark {
    position: absolute;
    left: 22px; top: 34px;
    width: 120px;
    font-size: 22px;
    flex-direction: column;
    align-items: flex-start;
  }
  .card-main .wordmark-dot { width: 24px; height: 24px; }
  .card-title {
    position: absolute;
    left: 156px; top: 26px;
    font-family: "Nunito", sans-serif;
    font-weight: 800;
    font-size: 27px;
    color: var(--brand-blue);
    white-space: nowrap;
  }
  .card-tagline {
    position: absolute;
    left: 158px; right: 20px; top: 70px;
    text-align: right;
    font-size: 11px;
    padding-bottom: 3px;
    border-bottom: 1.5px solid var(--ink);
  }
  .card-person {
    position: absolute;
    left: 250px; top: 110px;
    width: 120px;
    text-align: center;
  }
  .card-name {
    font-family: "Nunito", sans-serif;
    font-weight: 800;
    font-size: 17px;
  }
  .card-name .honorific { color: var(--brand-blue); }
  .card-name .surname { color: var(--brand-orange); }
  .card-role { font-size: 12px; font-weight: 700; }
  .card-footer {
    height: 80px;
    background: linear-gradient(90deg, var(--band-gold) 0%, var(--band-pale) 40%, var(--band-pale) 60%, var(--band-gold) 100%);
    border-top: 1px solid var(--edge);
    display: flex;
    justify-content: space-between;
    align-items: center;
    padding: 0 18px 0 22px;
  }
  .card-footer .contact-list li { font-size: 10px; }
  .card-footer .contact-list li + li { margin-top: 8px; }
</style>
</head>
<body>

<svg width="0" height="0" style="position:absolute" aria-hidden="true">
  <defs>
    <symbol id="icon-mobile" viewBox="0 0 16 16">
      <rect x="4" y="1" width="8" height="14" rx="2" fill="none" stroke="#111" stroke-width="1.6"/>
      <circle cx="8" cy="12.3" r="0.9" fill="#111"/>
    </symbol>
    <symbol id="icon-phone" viewBox="0 0 16 16">
      <path d="M1 6 Q8 1 15 6 L13 8 L11 7 L11 5.5 Q8 4.5 5 5.5 L5 7 L3 8 Z" fill="#111"/>
      <rect x="3" y="8.5" width="10" height="6" rx="1" fill="#111"/>
    </symbol>
    <symbol id="icon-hash" viewBox="0 0 16 16">
      <path d="M6 2 L5 14 M11 2 L10 14 M2 6 H14 M2 10.5 H14" stroke="#111" stroke-width="1.8" fill="none"/>
    </symbol>
    <symbol id="icon-home" viewBox="0 0 16 16">
      <path d="M1 8 L8 2 L15 8 Z" fill="#3a6fd0"/>
      <rect x="3" y="8" width="10" height="7" fill="#111"/>
    </symbol>
    <symbol id="icon-mail" viewBox="0 0 16 16">
      <rect x="1" y="3" width="14" height="10" fill="none" stroke="#111" stroke-width="1.6"/>
      <path d="M1 3 L8 9 L15 3" fill="none" stroke="#111" stroke-width="1.6"/>
    </symbol>
  </defs>
</svg>

<article class="letterhead">
  <header class="letterhead-header">
    <div class="wordmark"><span class="wordmark-dot"></span>Crossing the Stream</div>
    <h1 class="letterhead-title">Crossing the Stream</h1>
    <p class="letterhead-tagline">... Computer Training for Educators</p>
    <p class="date-line">Date: <span class="rule"></span></p>
  </header>
  <main class="letterhead-body"></main>
  <footer class="letterhead-footer">
    <ul class="contact-list">
      <li><svg><use href="#icon-mobile"/></svg>021 839 415</li>
      <li><svg><use href="#icon-phone"/></svg>0508 PCS MENTOR</li>
      <li><svg><use href="#icon-hash"/></svg>14 Kowhai Terrace, Riverhill, 4820</li>
    </ul>
    <ul class="contact-list">
      <li><svg><use href="#icon-home"/></svg>www.crossingthestream.co.nz</li>
      <li><svg><use href="#icon-mail"/></svg>training@crossingthestream.co.nz</li>
    </ul>
  </footer>
</article>

<article class="business-card">
  <div class="card-main">
    <div class="wordmark"><span class="wordmark-dot"></span>Crossing the Stream</div>
    <h2 class="card-title">Crossing the Stream</h2>
    <p class="card-tagline">... Computer Training for Educators</p>
    <div class="card-person">
      <p class="card-name"><span class="honorific">Mr.</span> <span class="surname">Manager</span></p>
      <p class="card-role">CEO</p>
    </div>
  </div>
  <footer class="card-footer">
    <ul class="contact-list">
      <li><svg><use href="#icon-mobile"/></svg>021 839 415</li>
      <li><svg><use href="#icon-phone"/></svg>0508 PCS MENTOR</li>
      <li><svg><use href="#icon-hash"/></svg>14 Kowhai Terrace, Riverhill, 4820</li>
    </ul>
    <ul class="contact-list">
      <li><svg><use href="#icon-home"/></svg>www.crossingthestream.co.nz</li>
      <li><svg><use href="#icon-mail"/></svg>training@crossingthestream.co.nz</li>
    </ul>
  </footer>
</article>

</body>
</html>
```